Belmont Ridge Business Card Design Project

We have recently rebranded and would like to design new business cards that incorporate the corporate logo - double sided cards with corporate logo on one side and contact details on the other

Target Market(s)

Sophisticated and high net worth investors and finance industry professionals

Industry/Entity Type

Funds Management

Contact Information for Business Card

The card should prominently feature the company name and logo. Other details will be standard contact details for each staff member - name, address, phone, email, website

Colors
0054AA
0677BA
7BADD7
CADEEF
E8F1F8

Requirements
Must have
• Double-sided design with one side prominently featuring the corporate logo and the other side with all standard contact details

```html
<!DOCTYPE html>
<html lang="en">
<head>
<meta charset="utf-8">
<title>Belmont Ridge – Business Card</title>
<link href="https://fonts.googleapis.com/css2?family=Arimo:wght@400;700&display=swap" rel="stylesheet">
<style>
  :root {
    --stage: #1b1b1b;
    --card: #204370;
    --motif-light: #25528a;
    --ink: #ffffff;
  }
  html, body {
    margin: 0;
    padding: 0;
    width: 1075px;
    height: 1200px;
    overflow: hidden;
    background: var(--stage);
    font-family: "Arimo", Arial, sans-serif;
    color: var(--ink);
  }
  .canvas { position: relative; width: 1075px; height: 1200px; }
  .card {
    position: absolute;
    width: 663px;
    height: 394px;
    background: var(--card);
    overflow: hidden;
  }
  .card--front { left: 206px; top: 187px; }
  .card--back { left: 203px; top: 637px; }

  .motif {
    position: absolute;
    right: 0;
    top: 0;
    width: 360px;
    height: 394px;
    background: linear-gradient(120deg, var(--card) 0%, var(--motif-light) 55%, var(--card) 100%);
  }

  .holder { position: absolute; left: 36px; top: 52px; }
  .holder__name { margin: 0; font-size: 24px; font-weight: 700; line-height: 1.1; letter-spacing: 0.2px; }
  .holder__role { margin: 2px 0 0; font-size: 17px; font-weight: 400; }

  .address {
    position: absolute;
    left: 36px;
    top: 153px;
    margin: 0;
    font-style: normal;
    font-size: 17px;
    line-height: 23.5px;
  }

  .contacts {
    position: absolute;
    left: 36px;
    top: 297px;
    margin: 0;
    padding: 0;
    list-style: none;
    font-size: 17px;
    line-height: 23.5px;
  }
  .contacts li { display: flex; align-items: center; gap: 6px; }
  .contacts svg { width: 17px; height: 17px; flex: none; }

  .brand {
    position: absolute;
    left: 0;
    right: 0;
    top: 222px;
    margin: 0;
    text-align: center;
    font-size: 54px;
    font-weight: 400;
    letter-spacing: 2px;
    text-transform: uppercase;
    line-height: 1;
  }
</style>
</head>
<body>
<main class="canvas">
  <section class="card card--front" aria-label="Card front with contact details">
    <div class="motif" role="img" aria-label="Large decorative brand motif in soft blue tones"></div>
    <div class="holder">
      <h1 class="holder__name">DANIEL HARTLEY</h1>
      <p class="holder__role">Managing Director</p>
    </div>
    <address class="address">
      87, Harbour Street<br>
      Suite 12<br>
      20450,Australia
    </address>
    <ul class="contacts">
      <li>
        <svg viewBox="0 0 24 24" aria-hidden="true"><path fill="#fff" d="M6.6 10.8a15.2 15.2 0 0 0 6.6 6.6l2.2-2.2a1 1 0 0 1 1-.25 11.4 11.4 0 0 0 3.6.57 1 1 0 0 1 1 1V20a1 1 0 0 1-1 1A17 17 0 0 1 3 4a1 1 0 0 1 1-1h3.5a1 1 0 0 1 1 1c0 1.25.2 2.45.57 3.57a1 1 0 0 1-.25 1z"/></svg>
        044-987 654 321
      </li>
      <li>
        <svg viewBox="0 0 24 24" aria-hidden="true"><path fill="#fff" d="M2 5h20v14H2z"/><path fill="none" stroke="#204370" stroke-width="1.6" d="M2 5l10 8 10-8M2 19l7.5-7M22 19l-7.5-7"/></svg>
        info@belmontridge.com
      </li>
      <li>
        <svg viewBox="0 0 24 24" aria-hidden="true"><g fill="none" stroke="#fff" stroke-width="1.8"><circle cx="12" cy="12" r="9.5"/><ellipse cx="12" cy="12" rx="4.2" ry="9.5"/><path d="M2.5 12h19M4 7h16M4 17h16"/></g></svg>
        www.belmontridge.com
      </li>
    </ul>
  </section>

  <section class="card card--back" aria-label="Card back with company name">
    <p class="brand">Belmont Ridge</p>
  </section>
</main>
</body>
</html>
```